Non fiction leadership Book Cover design needed for “Stay Bold: Build On Lasting Discipline”

I need a front cover design for a new book 6 X 9 traditional non-fiction book.

Title: "Stay BOLD - Build On Lasting Discipline"

The subtitle is not finalized- so use 2 lines of smaller dummy text

My brand guide is attached (please use the tan color sparingly)

I'd like to see BOLD look like it is in motion and "flying" across the page

Need CREATIVE designs and options

Do not want my picture on the front cover - I do want it on the back cover.

On the front cover I’d like to see creative use of font to create movement on “BOLD”

Target Market(s)

Business leaders

Industry/Entity Type

Aviation

Font styles to use
Other font styles liked:
• See style guide- can add additional font (modern script or san serif)

Colors
0054AA
0677BA
7BADD7
CADEEF
E8F1F8
EB3D1F
EC4F4E
F09395
F8D3D4
FCEDEE

Requirements
Must have
• Creative font use, using perspective to create movement/motion on BOLD
Should not have
• My picture on the front cover- my picture should be on the back cover

```html
<!DOCTYPE html>
<html lang="en">
<head>
<meta charset="utf-8">
<title>Stay Bold: Build On Lasting Discipline</title>
<link rel="stylesheet" href="https://fonts.googleapis.com/css2?family=Alegreya+Sans:wght@700;800;900&family=Kaushan+Script&display=swap">
<style>
  :root {
    --red-core: #f50f1e;
    --red-mid: #e80b1a;
    --red-edge: #b9000f;
    --white: #ffffff;
    --ghost-strong: rgba(255, 255, 255, 0.32);
    --ghost-soft: rgba(255, 255, 255, 0.14);
    --wing-gold: #f8c050;
    --wing-gold-fade: rgba(248, 192, 80, 0);
    --author-tan: #c99a55;
  }
  html, body {
    margin: 0;
    padding: 0;
    width: 800px;
    height: 1200px;
    overflow: hidden;
  }
  .cover {
    position: relative;
    width: 800px;
    height: 1200px;
    overflow: hidden;
    background: radial-gradient(ellipse 75% 60% at 50% 55%, var(--red-core) 0%, var(--red-mid) 55%, var(--red-edge) 100%);
    color: var(--white);
    font-family: "Alegreya Sans", "Helvetica Neue", Arial, sans-serif;
  }

  /* Wing artwork areas: soft gold placeholders */
  .wing-art {
    position: absolute;
    height: 44px;
    border-radius: 22px;
  }
  .wing-art--left {
    left: 12px;
    top: 100px;
    width: 120px;
    background: linear-gradient(90deg, var(--wing-gold-fade) 0%, var(--wing-gold) 55%, var(--wing-gold) 100%);
  }
  .wing-art--right {
    left: 676px;
    top: 140px;
    width: 120px;
    background: linear-gradient(90deg, var(--wing-gold) 0%, var(--wing-gold) 45%, var(--wing-gold-fade) 100%);
  }

  .title-script {
    position: absolute;
    top: 92px;
    left: 0;
    width: 800px;
    margin: 0;
    text-align: center;
    font-family: "Kaushan Script", "Brush Script MT", cursive;
    font-weight: 400;
    font-size: 150px;
    line-height: 1;
    white-space: nowrap;
    letter-spacing: -2px;
  }
  .title-script__motion {
    display: inline-block;
    margin-left: 14px;
    transform-origin: left center;
    transform: perspective(420px) rotateY(-22deg) skewX(-10deg) scaleX(1.05);
    text-shadow:
      -14px 4px 0 var(--ghost-strong),
      -30px 8px 0 var(--ghost-soft);
  }

  .title-kicker {
    position: absolute;
    top: 280px;
    left: 0;
    width: 800px;
    text-align: center;
    font-weight: 800;
    font-size: 104px;
    line-height: 1;
    white-space: nowrap;
  }
  .title-main {
    position: absolute;
    top: 350px;
    left: 0;
    width: 800px;
    text-align: center;
    font-weight: 900;
    font-size: 210px;
    line-height: 1;
    letter-spacing: -6px;
    white-space: nowrap;
  }
  .title-sub {
    position: absolute;
    top: 590px;
    left: 0;
    width: 800px;
    text-align: center;
    font-weight: 900;
    font-size: 150px;
    line-height: 1;
    letter-spacing: -3px;
    white-space: nowrap;
  }
  .divider {
    position: absolute;
    top: 793px;
    left: 335px;
    width: 128px;
    height: 2px;
    background: var(--white);
  }
  .subtitle {
    position: absolute;
    top: 826px;
    left: 0;
    width: 800px;
    margin: 0;
    text-align: center;
    font-weight: 700;
    font-size: 42px;
    line-height: 51px;
    letter-spacing: 6px;
    white-space: nowrap;
  }
  .author {
    position: absolute;
    top: 1056px;
    left: 0;
    width: 800px;
    text-align: center;
    font-weight: 800;
    font-size: 46px;
    letter-spacing: 4px;
    color: var(--author-tan);
    text-transform: uppercase;
    white-space: nowrap;
  }
</style>
</head>
<body>
<main class="cover">
  <div class="wing-art wing-art--left" role="img" aria-label="Golden wing illustration on the left of the script title"></div>
  <div class="wing-art wing-art--right" role="img" aria-label="Golden wing illustration on the right of the script title"></div>

  <h1 class="title-script">Stay<span class="title-script__motion">bold</span></h1>
  <div class="title-kicker">- Build On -</div>
  <div class="title-main">Lasting</div>
  <div class="title-sub">Discipline</div>

  <div class="divider"></div>

  <p class="subtitle">Unlock Your<br>Inner Potential and Soar to<br>New Heights</p>

  <div class="author">Margaret Holloway</div>
</main>
</body>
</html>
```